New Business Card Design Project

We require a business card design for Vexalund, a newly established Indian company.
Our focus is on the development, manufacturing, and export of a diverse array of pharmaceutical products on a global scale. The card should convey a professional appearance, as our primary markets are in Africa, China, and Southeast Asian nations.
We envision a two-sided business card, with the reverse side dedicated to a logo set against a solid color or an elegantly designed pattern. The corners should be rounded. We would appreciate seeing both horizontal and vertical design options. We trust the designer to utilize their expertise in creating this design.

The content for the business card is included in the attached Word file.

Target Market(s)

Our primary markets are in Africa, China, and Southeast Asian, Latin America, Maldives, Sri Lanka

Industry/Entity Type

Pharmaceutical Manufacturing and Export

Contact Information for Business Card

Colors

Designer to choose colors to be used in the design.

Requirements
Must have
• The reverse side of the business card features solely the logo along with the tagline, "Care in Every Dose."
Should not have
• The logo should not exceed two instances, encompassing both the front and back sides of the card.

```html
<!DOCTYPE html>
<html lang="en">
<head>
<meta charset="utf-8">
<title>Vexalund Business Card</title>
<link rel="stylesheet" href="https://fonts.googleapis.com/css2?family=Open+Sans:wght@400;600;700&display=swap">
<style>
  :root {
    --stage: #222222;
    --card: #ffffff;
    --blue: #2aa6e0;
    --coral: #f0604b;
    --ink: #1c1c1c;
  }
  * { margin: 0; padding: 0; box-sizing: border-box; }
  html, body { width: 1200px; height: 780px; overflow: hidden; }
  body {
    background: var(--stage);
    font-family: "Open Sans", Arial, sans-serif;
    position: relative;
  }
  .card {
    position: absolute;
    top: 240px;
    width: 520px;
    height: 300px;
    background: var(--card);
    border-radius: 22px;
    box-shadow: 0 10px 30px rgba(0,0,0,.45);
    overflow: hidden;
  }
  .card--front { left: 50px; }
  .card--back { left: 630px; }

  .accent-bar {
    position: absolute; left: 0; top: 26px;
    width: 8px; height: 34px; background: var(--blue);
  }
  .holder { position: absolute; left: 22px; top: 24px; }
  .holder__name { font-size: 24px; line-height: 1.1; letter-spacing: .3px; }
  .holder__first { color: var(--blue); font-weight: 700; }
  .holder__rest { color: var(--coral); font-weight: 400; }
  .holder__role { font-size: 11px; color: var(--ink); margin-top: 2px; }

  .address {
    position: absolute; left: 22px; bottom: 26px;
    font-style: normal;
    font-size: 12px; line-height: 1.45; color: var(--ink);
  }

  .brand {
    font-weight: 700; color: var(--blue);
    display: flex; align-items: center; gap: 10px;
    line-height: 1;
  }
  .brand__dot { border-radius: 50%; background: var(--coral); flex: none; }
  .card--front .brand {
    position: absolute; right: 32px; top: 112px; font-size: 42px;
  }
  .card--front .brand__dot { width: 20px; height: 20px; }

  .contacts {
    position: absolute; right: 22px; bottom: 24px;
    list-style: none; text-align: right;
    font-size: 12.5px; line-height: 1.55; color: var(--ink);
  }
  .contacts li { display: flex; align-items: center; justify-content: flex-end; gap: 8px; }
  .contacts svg { width: 13px; height: 13px; flex: none; }

  .lockup {
    position: absolute; left: 50%; top: 108px; transform: translateX(-50%);
    display: flex; flex-direction: column; align-items: flex-start;
  }
  .card--back .brand { font-size: 54px; }
  .card--back .brand__dot { width: 26px; height: 26px; }
  .tagline {
    margin-top: 14px; padding-left: 4px;
    font-size: 13px; color: var(--ink); letter-spacing: .3px;
  }
</style>
</head>
<body>
  <section class="card card--front" aria-label="Card front">
    <span class="accent-bar"></span>
    <div class="holder">
      <p class="holder__name"><span class="holder__first">Ravindra</span> <span class="holder__rest">K. Soman</span></p>
      <p class="holder__role">CEO</p>
    </div>

    <div class="brand"><span>Vexalund</span><span class="brand__dot"></span></div>

    <address class="address">
      14, Nilgiri Nagar,<br>
      Wardhora, 441120, India
    </address>

    <ul class="contacts">
      <li>+91 93012 58674
        <svg viewBox="0 0 14 14" aria-hidden="true"><rect x="3" y="1" width="8" height="12" rx="1.5" fill="none" stroke="var(--coral)" stroke-width="1.5"/></svg>
      </li>
      <li>www.vexalund.com
        <svg viewBox="0 0 14 14" aria-hidden="true"><circle cx="7" cy="7" r="6" fill="var(--blue)"/><path d="M1 7h12M7 1c-3 3-3 9 0 12M7 1c3 3 3 9 0 12" fill="none" stroke="#fff" stroke-width=".9"/></svg>
      </li>
      <li>rsoman@vexalund.com
        <svg viewBox="0 0 14 14" aria-hidden="true"><rect x="1" y="3" width="12" height="9" rx="1" fill="var(--coral)"/><path d="M1.5 3.5 7 8l5.5-4.5" fill="none" stroke="#fff" stroke-width="1.1"/></svg>
      </li>
    </ul>
  </section>

  <section class="card card--back" aria-label="Card back">
    <div class="lockup">
      <div class="brand"><span>Vexalund</span><span class="brand__dot"></span></div>
      <p class="tagline">Care in Every Dose.</p>
    </div>
  </section>
</body>
</html>
```